Pine Ledge Traders, LLC- Global Beverage Company with 100% Cold Chain Logistics

Hey All, My Name is Dale, I am a young business owner in a competitive export space, but my niche is that I am shipping all of my beer around the world, "100% Cold Chain". This model is more costly, but it protects the integrity of the beer itself and will give folks in foreign countries the best representation of what US Craft Beer has to offer.

I am not a branding guy and don't claim to be one, I am a salesperson first, and will be referring to all of you to create something great that will be memorable.

I am looking for a basic Business Card Design for my Craft Beer Export company. I sell US Craft Beer in several countries around the globe. Austrailia, China, Taiwan, Chile, France, New Zealand... to name a few.

I am looking for a sleek, modern, and fresh design. Quickly!

Thanks for your consideration!

Cheers,

Dale

Target Market(s)

International

Contact Information for Business Card

Dale Corrigan
Founder- Roaming Hops Guy
Dale@PineLedgeTraders.example
@RoamingHopsGuy- Instagram only
www.Pineledgetraders.example
@PineLedgeTradersAU- Instagram Only

Font styles to use
Serif

Colors
0592cd
ffffff

Requirements
Must have
• Name-
• Title-
• Email-
• Social Media Handle-
• Company Website-
Nice to have
• Nice Logo/ Images on Card
Should not have
• Tacky Beer Images

```html
<!DOCTYPE html>
<html lang="en">
<head>
<meta charset="utf-8">
<title>Pine Ledge Traders – Business Card</title>
<link rel="stylesheet" href="https://fonts.googleapis.com/css2?family=Cinzel:wght@400;500&family=Roboto:wght@400&display=swap">
<style>
  :root {
    --brand-blue: #0592cd;
    --band-blue: #0a86bd;
    --card-white: #f3f4f5;
    --ink: #3a3d40;
    --muted: #6b6f73;
    --backdrop: #a9a9a9;
    --icon-blue: #2a8fd0;
    --social-navy: #3b5b98;
  }
  * { box-sizing: border-box; margin: 0; padding: 0; }
  html, body { width: 1200px; height: 900px; overflow: hidden; }
  body { background: var(--backdrop); position: relative; font-family: "Roboto", Arial, sans-serif; }

  .card {
    position: absolute; top: 200px; width: 310px; height: 502px;
    box-shadow: 2px 3px 6px rgba(0,0,0,.35);
    overflow: hidden;
  }
  .card--front { left: 308px; background: var(--card-white); border-radius: 52px 4px 52px 4px; }
  .card--back { left: 641px; background: var(--brand-blue); border-radius: 4px 52px 4px 52px; }

  .company-name {
    font-family: "Cinzel", Georgia, serif; font-weight: 400;
    color: var(--brand-blue); letter-spacing: .5px; line-height: 1.15;
    text-align: center; text-transform: uppercase;
  }
  .card--front .company-name { position: absolute; top: 110px; left: 70px; width: 240px; font-size: 26px; }

  .person { position: absolute; left: 27px; top: 330px; }
  .person__name {
    font-family: "Cinzel", Georgia, serif; font-size: 25px; color: var(--brand-blue);
    letter-spacing: .5px; line-height: 1;
  }
  .person__title { font-size: 14px; color: var(--ink); margin-top: 9px; }
  .contact-list { list-style: none; margin-top: 14px; font-size: 14px; color: var(--ink); }
  .contact-list li { display: flex; align-items: center; gap: 7px; height: 18px; }
  .contact-list li.social { margin-top: 18px; }
  .contact-list svg { flex: none; }

  .back-band { position: absolute; inset: 0; }
  .claim {
    position: absolute; top: 42px; width: 100%; text-align: center;
    font-family: "Cinzel", Georgia, serif; color: #fff;
  }
  .claim__figure { font-size: 25px; line-height: 1.1; }
  .claim__label { font-size: 17px; letter-spacing: .5px; }
  .markets {
    position: absolute; top: 164px; width: 100%; list-style: none; text-align: center;
    font-family: "Cinzel", Georgia, serif; color: #fff; font-size: 17px; line-height: 22.6px;
  }
  .card--back .company-name { position: absolute; top: 372px; left: 0; width: 100%; font-size: 29px; color: #fff; }
</style>
</head>
<body>

<section class="card card--front" aria-label="Card front">
  <p class="company-name">Pine Ledge Traders</p>

  <div class="person">
    <h1 class="person__name">Dale Corrigan</h1>
    <p class="person__title">Founder - Roaming Hops Guy</p>
    <ul class="contact-list">
      <li>
        <svg width="13" height="10" viewBox="0 0 13 10" aria-hidden="true">
          <rect x="0.5" y="0.5" width="12" height="9" fill="none" stroke="var(--icon-blue)"/>
          <path d="M0.5 0.5 L6.5 5.5 L12.5 0.5" fill="none" stroke="var(--icon-blue)"/>
        </svg>
        Dale@PineLedgeTraders.example
      </li>
      <li>
        <svg width="13" height="13" viewBox="0 0 13 13" aria-hidden="true">
          <circle cx="6.5" cy="6.5" r="6" fill="var(--icon-blue)"/>
          <path d="M3 4 Q6 3 7 6 Q5 8 7 11" fill="none" stroke="#fff" stroke-width="1.2"/>
        </svg>
        www.Pineledgetraders.example
      </li>
      <li class="social">
        <svg width="17" height="17" viewBox="0 0 17 17" aria-hidden="true">
          <rect width="17" height="17" fill="var(--social-navy)"/>
        </svg>
        @RoamingHopsGuy
      </li>
    </ul>
  </div>
</section>

<section class="card card--back" aria-label="Card back">
  <svg class="back-band" width="310" height="502" viewBox="0 0 310 502" aria-hidden="true">
    <polygon points="0,136 310,102 310,320 0,354" fill="var(--band-blue)"/>
  </svg>
  <div class="claim">
    <p class="claim__figure">100%</p>
    <p class="claim__label">Cold Chain Logistics</p>
  </div>
  <ul class="markets">
    <li>Austrailia</li>
    <li>China</li>
    <li>Taiwan</li>
    <li>Chile</li>
    <li>France</li>
    <li>New Zealand</li>
  </ul>
  <p class="company-name">Pine Ledge Traders</p>
</section>

</body>
</html>
```